Book Cover for a book on Quiet Ventures

I am self-publishing my book on Brindlecart and need a book cover made. Below are the details. See attached templates for size we need to use. I also attached a previous cover we had made that I liked. The problem with it was they were two boys helping each other but the book is about women. I'm open to your ideas on the cover though, but I wanted to show you a style I liked as an idea.
Front of Cover
Book Title: Quiet Ventures
Book Subtitle: Unvarnished Notes of a Woman Founder
Author Name: Lorna T. Pelham
Add on the Spine of Cover: Quiet Ventures and Lorna T. Pelham
Back of the Cover Text:
Quiet Ventures: Unvarnished Notes of a Woman Founder is an honest account of a business owner’s experience attempting to navigate the start-up community while also pursuing spiritual growth. Author Lorna Pelham defines a spiritual entrepreneur as “someone who runs an enterprise with the purpose of growing love rather than material gain.” This book discusses the three dimensions of Quiet Ventures:
1. The business is an integral part of the founder’s spiritual journey.
2. Employees working for the spiritual enterprise, whether they know it or not, encounter this company because it's part of their spiritual path.
3. The business itself has a life force of its own and its purpose is to further the kingdom of heaven on earth.
These three dimensions happen simultaneously and work together to produce the greatest possible result. However, this can feel confusing to a founder juggling these dimensions while also trying to manage and run a business. This is not a formulaic self-help book or roadmap. Rather, it is a compilation of personal reflections that often seem at odds with the traditional world of entrepreneurship.
Below the description add my picture (see attached for my picture)
Bio text:
Lorna Pelham founded Halvex with the vision of ushering in a life-long education system that shifts away from standardization to one that empowers people to live their purpose. In college, Lorna interned for Open Meadow, a women’s empowerment initiative where she recognized her passion for helping people find their voice. Lorna's 20-year journey has come full circle to empowering other female CEOs who are pursuing the path of Quiet Ventures.
NOTE: Please note that Brindlecart puts a bar code on the bottom right of the back cover as is noted on the attached template.
Size template is attached to the brief, here are the sizes typed out:
# Description Width (in) Height (in)
1 Full Cover 12.79 9.25
2 Front Cover 6 9
3 Safe Area 5.875 8.75
4 Bleed 0.125 0.125
5 Margin 0.125 0.125
6 Spine 0.54 9
7 Spine Safe Area 0.415 8.75
8 Spine Margin 0.062 0.062
9 Barcode Margin 0.25 0.25
Pre-publication checklist
BRINDLECART TIPS for the final cover:
1. Save as a PDF. Your cover must be a single PDF that includes the back cover, spine, and front cover as one image.
2. Flatten all transparencies. These can cause the file to print with missing or distorted content. Consult your software's documentation to learn how.
3. Embed your fonts. Consult your software's documentation to learn how.
4. Remove crop marks, color bars, template text. Crop marks are lines showing where pages should be trimmed. Color bars are strips with a series of patches used to ensure color balance during printing. Also, remove any template text, PDF creation guides, or software references.
5. Ensure your cover image meets the minimum resolution of 300 DPI (dots per inch).
6. Optimize PDFs. Optimization is useful to reduce your file size, allowing for higher performance when transferring, uploading, viewing, and printing the files.
7. Remove file security. Locked or encrypted files will fail review.
Target Market(s)
Women who want to be CEOs or are currently CEOs of companies.
Industry/Entity Type
Entrepreneurship, business, spirituality
Requirements
Must have
- Just the text on the description. A very welcoming feel.
Nice to have
- I like the idea of having a sunrise/sunset in the image somehow like in the example I attached to the brief, but again I'm open.
Should not have
- Please don't put any yoga or meditation poses or hands outstretched. I have a lot of interesting ones that look like my example so if you are going to submit after Saturday 10/29, please only do so if you have a new idea! Thanks!

```html
<!DOCTYPE html>
<html lang="en">
<head>
<meta charset="utf-8">
<title>Quiet Ventures – Book Cover</title>
<link href="https://fonts.googleapis.com/css2?family=Teko:wght@500&family=Rubik:wght@400&family=Tinos&display=swap" rel="stylesheet">
<style>
  :root{
    --page:#ffffff;
    --ink:#000000;
    --white:#ffffff;
    --gold-edge:#e8943a;
    --gold-mid:#f8e45c;
    --orange:#e8953a;
    --sky-top:#1b3a9a;
    --sky-mid:#4a6fd0;
    --sun:#f7d35a;
    --dusk:#e07a2a;
  }
  *{margin:0;padding:0;box-sizing:border-box}
  html,body{width:1200px;height:1200px;overflow:hidden;background:var(--page)}
  .canvas{position:relative;width:1200px;height:1200px}
  .cover{position:absolute;left:63px;top:211px;width:1074px;height:777px;background:var(--ink);overflow:hidden}
  .gold-text{
    background:linear-gradient(90deg,var(--gold-edge) 0%,var(--gold-mid) 50%,var(--gold-edge) 100%);
    -webkit-background-clip:text;background-clip:text;color:transparent;
  }
  .title-main{font-family:"Teko",sans-serif;font-weight:500;line-height:1;text-align:center;text-transform:uppercase}
  .title-sub{font-family:"Rubik",sans-serif;color:var(--orange);text-align:center;text-transform:uppercase;line-height:1}

  /* back cover */
  .back-title{position:absolute;left:41px;top:46px;width:470px;font-size:104px;letter-spacing:1px}
  .back-subtitle{position:absolute;left:41px;top:137px;width:470px;font-size:22px;letter-spacing:2px}
  .back-rule{position:absolute;left:71px;top:166px;width:371px;height:1px;background:linear-gradient(90deg,transparent,var(--white) 20%,var(--white) 80%,transparent)}
  .blurb{position:absolute;left:35px;top:178px;width:458px;font-family:"Tinos",serif;font-size:14px;line-height:17px;color:var(--white);text-align:justify}
  .blurb p{margin:0}
  .dimensions{list-style:none;margin:12px 0 7px 20px;width:420px}
  .dimensions li{position:relative;padding-left:10px;margin-bottom:9px;text-align:left}
  .dimensions li:last-child{margin-bottom:0}
  .dimensions li::before{content:"";position:absolute;left:0;top:7px;width:4px;height:4px;border-radius:50%;background:var(--orange)}
  .author-portrait{position:absolute;left:35px;top:495px;width:105px;height:118px;border:2px solid var(--orange);border-radius:3px;background:linear-gradient(160deg,#c9d9b0 0%,#8aa86a 45%,#e04a5a 100%)}
  .bio{position:absolute;left:154px;top:497px;width:340px;font-family:"Tinos",serif;font-size:14px;line-height:17px;color:var(--white);text-align:justify}

  /* spine */
  .spine-title{position:absolute;left:522px;top:64px;writing-mode:vertical-rl;font-size:44px;line-height:1;letter-spacing:1px}
  .spine-author{position:absolute;left:526px;top:506px;writing-mode:vertical-rl;font-family:"Tinos",serif;font-size:32px;color:var(--white);line-height:1}

  /* front cover */
  .front-scene{position:absolute;left:588px;top:0;width:486px;height:480px;
    background:
      linear-gradient(180deg,rgba(0,0,0,0) 55%,var(--ink) 100%),
      radial-gradient(ellipse 30% 16% at 50% 54%,var(--sun) 0%,rgba(247,211,90,0) 100%),
      linear-gradient(180deg,var(--sky-top) 0%,var(--sky-mid) 28%,#a47a8a 44%,var(--dusk) 54%,#3a2a20 66%,#111 100%)}
  .front-title{position:absolute;left:584px;top:448px;width:490px;font-size:150px;letter-spacing:2px}
  .front-subtitle{position:absolute;left:584px;top:581px;width:490px;font-size:30px;letter-spacing:3px}
  .front-rule{position:absolute;left:656px;width:337px;height:1px}
  .front-rule.top{top:619px;background:var(--white)}
  .front-rule.bottom{top:680px;background:var(--orange)}
  .tagline{position:absolute;left:584px;width:490px;font-family:"Rubik",sans-serif;font-size:21px;letter-spacing:6px;text-align:center;text-transform:uppercase;line-height:1}
  .tagline.first{top:628px;color:var(--white)}
  .tagline.second{top:653px;color:var(--orange)}
  .front-author{position:absolute;left:584px;top:692px;width:490px;font-family:"Tinos",serif;font-size:37px;line-height:1.1;color:var(--white);text-align:center}
</style>
</head>
<body>
<div class="canvas">
  <div class="cover">
    <!-- back cover -->
    <div class="back-title title-main gold-text">Quiet</div>
    <div class="back-subtitle title-sub">Ventures</div>
    <div class="back-rule"></div>
    <div class="blurb">
      <p>Unvarnished Notes of a Woman Founder is an honest account of a business owner’s experience attempting to navigate the start-up community while also pursuing spiritual growth. Author Lorna Pelham defines a spiritual entrepreneur as “someone who runs an enterprise with the purpose of growing love rather than material gain.” This book discusses the three dimensions of Quiet Ventures:</p>
      <ul class="dimensions">
        <li>The business is an integral part of the founder’s spiritual journey.</li>
        <li>Employees working for the spiritual enterprise, whether they know it or not, encounter this company because it's part of their spiritual</li>
        <li>The business itself has a life force of its own and its purpose is to further the kingdom of heaven on earth.</li>
      </ul>
      <p>These three dimensions happen simultaneously and work together to produce the greatest possible result. However, this can feel confusing to a founder juggling these dimensions while also trying to manage and run a business. This is not a formulaic self-help book or roadmap. Rather, it is a compilation of personal reflections that often seem at odds with the traditional world of entrepreneurship.</p>
    </div>
    <div class="author-portrait" role="img" aria-label="Portrait photo of the author outdoors"></div>
    <p class="bio">Lorna Pelham founded Halvex with the vision of ushering in a life-long education system that shifts away from standardization to one that empowers people to live their purpose. In college, Lorna interned for Open Meadow, a women’s empowerment initiative where she recognized her passion for helping people find their voice. Lorna's 20-year journey has come full circle to empowering other female CEOs who are pursuing the path of Quiet Ventures.</p>

    <!-- spine -->
    <div class="spine-title title-main gold-text">Quiet Ventures</div>
    <div class="spine-author">Lorna T. Pelham</div>

    <!-- front cover -->
    <div class="front-scene" role="img" aria-label="Silhouettes of two hikers helping each other up a seaside rock at sunset"></div>
    <div class="front-title title-main gold-text">Quiet</div>
    <div class="front-subtitle title-sub">Ventures</div>
    <div class="front-rule top"></div>
    <div class="tagline first">Unvarnished Notes of</div>
    <div class="tagline second">A Woman Founder</div>
    <div class="front-rule bottom"></div>
    <div class="front-author">Lorna T. Pelham</div>
  </div>
</div>
</body>
</html>
```